Harborline Auto LLC

Car Dealer Customer Service
Address: 2874 Cresthaven Road, Alderbrook, XQ 48210
web: www.harborlineautoxq.net
email: harborlineautoxq@mailnest.example
Phone: (555) 555-0148
Phone: (555) 555-0173

```html
<!DOCTYPE html>
<html lang="en">
<head>
<meta charset="utf-8">
<title>Harborline Auto – Business Card</title>
<link rel="stylesheet" href="https://fonts.googleapis.com/css2?family=Montserrat:wght@400;500;700&display=swap">
<style>
  :root {
    --backdrop: #3b3b3b;
    --card: #1a1a1a;
    --edge-blue: #2a8ac6;
    --brand-blue: #2a8ac6;
    --accent-yellow: #f0b43c;
    --text-light: #f2f2f2;
  }
  * { margin: 0; padding: 0; box-sizing: border-box; }
  html, body {
    width: 1200px; height: 801px; overflow: hidden;
    background: var(--backdrop);
    font-family: "Montserrat", Arial, sans-serif;
  }
  .stage {
    position: relative; width: 1200px; height: 801px;
    display: flex; align-items: center; justify-content: center; gap: 40px;
  }
  .card {
    position: relative; width: 540px; height: 309px;
    background: var(--card);
    border-left: 3px solid var(--edge-blue);
    border-bottom: 3px solid var(--edge-blue);
    box-shadow: 0 14px 30px rgba(0,0,0,.35);
  }
  .brand {
    position: absolute; left: 0; right: 0; top: 62px;
    display: flex; align-items: center; justify-content: center; gap: 12px;
    padding-right: 90px;
  }
  .brand-dot { width: 22px; height: 22px; border-radius: 50%; background: var(--brand-blue); flex: none; }
  .brand-name {
    color: var(--brand-blue); font-weight: 700; font-size: 27px;
    letter-spacing: .5px; text-transform: uppercase; white-space: nowrap;
  }
  .tagline-row {
    position: absolute; left: 28px; right: 28px; top: 140px;
    display: flex; align-items: center; gap: 10px;
  }
  .tagline-rule { height: 2px; background: var(--accent-yellow); }
  .tagline-rule.short { width: 110px; }
  .tagline-rule.long { flex: 1; }
  .tagline {
    color: var(--brand-blue); font-weight: 700; font-size: 15px;
    text-transform: uppercase; white-space: nowrap;
  }
  .contacts {
    position: absolute; left: 34px; top: 196px;
    list-style: none; color: var(--text-light); font-size: 13px; line-height: 24px;
  }
  .contacts li { display: flex; align-items: center; gap: 8px; white-space: nowrap; }
  .contacts svg { width: 12px; height: 12px; fill: var(--accent-yellow); flex: none; }
  .location {
    position: absolute; right: 30px; top: 196px;
    color: var(--text-light); font-size: 13px; line-height: 22px; font-style: normal;
    white-space: nowrap;
  }
  .location .web { color: var(--accent-yellow); font-weight: 500; }
  .card-back .brand-back {
    position: absolute; inset: 0;
    display: flex; align-items: center; justify-content: center; gap: 14px;
  }
  .card-back .brand-name { font-size: 30px; }
  .card-back .brand-dot { width: 26px; height: 26px; }
</style>
</head>
<body>
<main class="stage">
  <section class="card card-front" aria-label="Business card front">
    <div class="brand">
      <span class="brand-dot"></span>
      <span class="brand-name">Harborline Auto</span>
    </div>
    <div class="tagline-row">
      <span class="tagline-rule short"></span>
      <span class="tagline">Car Dealer Customer Service</span>
      <span class="tagline-rule long"></span>
    </div>
    <ul class="contacts">
      <li><svg viewBox="0 0 24 24"><path d="M6.6 10.8a15 15 0 0 0 6.6 6.6l2.2-2.2a1 1 0 0 1 1-.25 11.4 11.4 0 0 0 3.6.57 1 1 0 0 1 1 1V20a1 1 0 0 1-1 1A17 17 0 0 1 3 4a1 1 0 0 1 1-1h3.5a1 1 0 0 1 1 1c0 1.25.2 2.45.57 3.6a1 1 0 0 1-.25 1z"/></svg>(555) 555-0148</li>
      <li><svg viewBox="0 0 24 24"><path d="M6.6 10.8a15 15 0 0 0 6.6 6.6l2.2-2.2a1 1 0 0 1 1-.25 11.4 11.4 0 0 0 3.6.57 1 1 0 0 1 1 1V20a1 1 0 0 1-1 1A17 17 0 0 1 3 4a1 1 0 0 1 1-1h3.5a1 1 0 0 1 1 1c0 1.25.2 2.45.57 3.6a1 1 0 0 1-.25 1z"/></svg>(555) 555-0173</li>
      <li><svg viewBox="0 0 24 24"><path d="M2 5h20v14H2z M2 5l10 8 10-8"/></svg>harborlineautoxq@mailnest.example</li>
    </ul>
    <address class="location">
      2874 Cresthaven Road<br>
      Alderbrook, XQ 48210<br>
      <span class="web">www.harborlineautoxq.net</span>
    </address>
  </section>

  <section class="card card-back" aria-label="Business card back">
    <div class="brand-back">
      <span class="brand-dot"></span>
      <span class="brand-name">Harborline Auto</span>
    </div>
  </section>
</main>
</body>
</html>
```